http://www.brindlewares.com/ New Ecommerce Site

We are redesigning Brindlewares.com on shopvantly.com.

We need to get a design for the ecommerce site.

They have about 15-45 products and these are the menu items that they need on the pages.

Knives:
Kitchen Knives
Neck Knives
Outdoor Knives
Bluefinch Knives
Clearance Knives
Premium Knives
Misc. Product:
Waterstones
Books
DVDs
T-Shirts
Scissors
Bladesmithing School
Videos
Links
Testimonials/Feedback
Contact Dennis Form
Knife Care and Maintenance Tips
Knife Sharpening
Knife Archives
Kitchen Knife Archives

We need several pages designed.

- Category Page
- Single Item page
- Knive Archive Pages (This is where old knives are stored that are not being sold anymore)
- Featured Product pages.
- Information pages
- checkout

The design has to be VERY elagant, like vostel.com.
And it has to be very easy to navigate and buy items like http://bladesgoquick.com/

Thanks,
Peter Hollis

Requirements
Must have
• Must be very elegant, and have the menu items somewhere on the pages.

```html
<!DOCTYPE html>
<html lang="en">
<head>
<meta charset="utf-8">
<title>Brindle Wares</title>
<link href="https://fonts.googleapis.com/css2?family=PT+Sans:wght@400;700&family=Questrial&display=swap" rel="stylesheet">
<style>
:root{
  --orange:#f28a1a;
  --orange-dark:#e06f08;
  --panel-grey:#8c8c8c;
  --ink:#333;
  --line:#dcdcdc;
  --footer:#262626;
  --brand-grey:#8f8f8f;
  --white:#fff;
}
*{box-sizing:border-box;margin:0;padding:0}
html,body{width:972px;height:1200px;overflow:hidden}
body{position:relative;background:var(--white);font-family:"PT Sans",sans-serif;color:var(--ink)}
.abs{position:absolute}

.site-header{left:0;top:0;width:972px;height:110px;background:linear-gradient(#fafafa,#e8e8e8)}
.brand{left:87px;top:11px;font-family:"PT Sans",sans-serif;font-weight:400;color:var(--brand-grey);font-size:37px;line-height:35px;letter-spacing:2px}
.brand-tag{left:88px;top:89px;font-size:10.5px;color:#555}
.phone{left:731px;top:34px;display:flex;align-items:center;gap:6px;color:var(--orange);font-family:"Questrial",sans-serif;font-size:21px}
.phone svg{display:block}
.search{left:731px;top:70px;width:140px;height:24px;background:#fff;border-radius:4px;box-shadow:0 1px 2px rgba(0,0,0,.15);font-size:11px;color:#999;padding:5px 9px}
.search svg{position:absolute;right:7px;top:4px}

.main-nav{left:0;top:110px;width:972px;height:54px;background:linear-gradient(#7d7d7d,#959595)}
.main-nav a{position:absolute;top:19px;color:var(--white);font-size:14px;text-decoration:none}
.cart{left:742px;top:123px;width:127px;height:33px;background:#9a9a9a;border-radius:4px;color:#fff;font-size:14px;display:flex;align-items:center;gap:10px;padding-left:10px}

.quick-order{left:945px;top:170px;width:27px;height:100px;background:#111;border-radius:6px 0 0 6px;color:#fff;font-size:12px;writing-mode:vertical-rl;display:flex;align-items:center;justify-content:center}

.box{background:#fff;border:1px solid var(--line)}
.welcome{left:84px;top:168px;width:124px;height:183px;padding:3px}
.welcome-inner{background:var(--panel-grey);height:100%;color:#fff;padding:12px 7px}
.welcome h2{font-family:"Questrial",sans-serif;font-weight:400;font-size:14px;line-height:19px;text-align:center;margin-bottom:10px}
.welcome p{font-size:9px;line-height:14.5px;text-align:justify}
.btn{display:inline-block;background:linear-gradient(#f9a035,var(--orange-dark));color:#fff;border-radius:4px;text-align:center}
.welcome .btn{margin:8px 0 0 12px;width:81px;height:21px;font-size:11.5px;line-height:21px}
.guarantee{left:84px;top:357px;width:124px;height:178px;padding:13px 8px}
.guarantee h3{font-family:"Questrial",sans-serif;font-weight:400;color:#d9342b;font-size:13.5px;text-align:center;margin-bottom:14px}
.guarantee p{font-size:9px;line-height:14.5px;text-align:justify}

.slider{left:215px;top:168px;width:463px;height:367px;padding:3px}
.slide-photo{width:100%;height:100%;background:
  radial-gradient(ellipse 45% 60% at 40% 35%,rgba(110,50,35,.75),transparent 70%),
  radial-gradient(ellipse 50% 20% at 55% 45%,rgba(225,225,225,.55),transparent 70%),
  linear-gradient(135deg,#a99478,#8f7a60 50%,#a08a6c);position:relative}
.caption{position:absolute;left:3px;right:3px;top:245px;height:81px;background:rgba(30,30,30,.85);color:#fff;font-family:"Questrial",sans-serif;font-size:10.5px;line-height:19.5px;padding:20px 50px 0 42px}
.arrow{position:absolute;top:31px;width:24px;height:24px;border-radius:50%;background:#777}
.arrow svg{display:block;margin:7px}
.arrow.prev{left:13px}.arrow.next{right:13px}

.signup{left:684px;top:168px;width:204px;height:279px;padding:4px 7px}
.signup h2{font-weight:400;font-size:17px}
.signup h2 .free{color:var(--orange);font-weight:700;letter-spacing:1px}
.signup h3{font-weight:400;font-size:13.5px;margin-top:1px}
.signup .lede{font-size:9.5px;line-height:14.5px;margin-top:13px}
.field{width:178px;height:24px;border:1px solid #ccc;font-size:9px;color:#999;padding:5px 8px;margin:4px 0 0 3px}
.field.first{margin-top:23px}
.signup .btn{width:175px;height:21px;line-height:21px;font-size:12.5px;margin:7px 0 0 5px;border-radius:5px}
.signup .note{font-size:9.5px;line-height:14.5px;margin:13px 8px 0 5px;text-align:justify}

.products-tab{left:684px;top:455px;width:204px;height:81px;display:flex}
.products-tab span{flex:1;font-family:"Questrial",sans-serif;font-size:20px;color:#555;line-height:79px;padding-left:20px}
.products-tab i{width:58px;background:linear-gradient(#f8a031,var(--orange-dark));display:flex;align-items:center;justify-content:center}

.section-title{left:90px;top:543px;font-family:"Questrial",sans-serif;font-weight:400;font-size:15.5px;color:#222}
.section-title em{font-style:normal;color:var(--orange);font-size:19px}

.card{width:189px;height:171px;border:1px solid #ccc;overflow:hidden}
.card .photo{width:100%;height:100%}
.price-bar{position:absolute;left:0;right:0;bottom:0;height:30px;background:rgba(20,20,20,.82);display:flex;align-items:center;justify-content:space-between;padding:0 16px 0 17px}
.price-bar b{color:#fff;font-size:12.5px}
.price-bar .btn{font-size:9px;width:65px;height:22px;line-height:22px;border-radius:3px}

.feature-strip{left:93px;top:957px;width:780px;height:74px;border:1px solid #ccc;border-radius:6px}
.feature{position:absolute;top:14px;display:flex;align-items:center;gap:12px;font-family:"Questrial",sans-serif;color:var(--orange);font-size:19px;line-height:23px}

.site-footer{left:0;top:1049px;width:972px;height:151px;background:var(--footer);color:#ddd;font-size:10.5px}
.site-footer h4{position:absolute;font-size:11px;color:#fff;top:22px}
.f-links{position:absolute;top:50px;line-height:19.5px}
.socials{position:absolute;left:436px;top:58px;display:flex;gap:12px}
.socials span{width:26px;height:26px;border-radius:4px;background:linear-gradient(#4d7bc7,#2c5aa3)}
.social-text{position:absolute;left:436px;top:94px}
.f-brand{position:absolute;left:737px;top:19px;font-family:"PT Sans",sans-serif;font-weight:400;color:#5a5a5a;font-size:27px;line-height:26px;letter-spacing:1.5px}
.f-tag{position:absolute;left:738px;top:74px;font-size:7.5px;color:#777}
.copy{position:absolute;left:629px;top:94px}
</style>
</head>
<body>

<header class="site-header abs">
  <div class="brand abs">BRINDLE<br>WARES</div>
  <div class="brand-tag abs">17th Generation Tanabe Bladesmith</div>
  <div class="phone abs">
    <svg width="20" height="20" viewBox="0 0 20 20"><rect width="20" height="20" rx="3" fill="#f28a1a"/><path d="M6 4l2.5 0 1 3-1.5 1.2c.8 1.8 2 3 3.8 3.8L13 10.5l3 1V14c0 1-1 2-2 2C8.5 15.5 4.5 11.5 4 6c0-1 1-2 2-2z" fill="#fff"/></svg>
    1300 555 019
  </div>
  <div class="search abs">Search
    <svg width="16" height="16" viewBox="0 0 16 16"><circle cx="6.5" cy="6.5" r="5" fill="none" stroke="#5a7ea6" stroke-width="1.6"/><path d="M10 10l5 5" stroke="#555" stroke-width="2.2"/></svg>
  </div>
</header>

<nav class="main-nav abs">
  <a style="left:108px">Home</a>
  <a style="left:181px">Knives</a>
  <a style="left:254px">Tools</a>
  <a style="left:321px">Instruction</a>
  <a style="left:420px">About</a>
  <a style="left:492px">Contact Dennis</a>
</nav>
<div class="cart abs">
  <svg width="36" height="24" viewBox="0 0 36 24"><path d="M2 4h6l4 12h16l4-9H10" fill="none" stroke="#e5e5e5" stroke-width="2"/><circle cx="14" cy="20" r="2" fill="#e5e5e5"/><circle cx="26" cy="20" r="2" fill="#e5e5e5"/></svg>
  Your Cart
</div>

<div class="quick-order abs">Quick Order</div>

<aside class="welcome box abs">
  <div class="welcome-inner">
    <h2>Welcome to Brindle Wares</h2>
    <p>your source of high performance hand-forged cutlery and world renowned sharp-ening instruction!</p>
    <span class="btn">Read more</span>
  </div>
</aside>
<aside class="guarantee box abs">
  <h3>Guarantee !</h3>
  <p>Lorem ipsum dolor sit amet, consectetur adipis-icing elit, sed do eiusmod tempor incididunt ut labore et dolore magna aliqua. Ut enim ad minim veniam,</p>
</aside>

<section class="slider box abs">
  <div class="slide-photo" role="img" aria-label="Hunting knife with stag handle resting on a tooled leather sheath over burlap"></div>
  <div class="caption">
    Lorem ipsum dolor sit amet, consectetur adipisicing elit, sed do eiusmod tempor incididunt ut labore et dolore magna aliqua.
    <span class="arrow prev"><svg width="10" height="10" viewBox="0 0 10 10"><path d="M7 1L3 5l4 4" fill="none" stroke="#fff" stroke-width="2"/></svg></span>
    <span class="arrow next"><svg width="10" height="10" viewBox="0 0 10 10"><path d="M3 1l4 4-4 4" fill="none" stroke="#fff" stroke-width="2"/></svg></span>
  </div>
</section>

<section class="signup box abs">
  <h2>Read your <span class="free">FREE</span></h2>
  <h3>Knife Care Tips</h3>
  <p class="lede">Subscribe for Dennis's Free Knife Care and Maintenance Tips:</p>
  <div class="field first">Name</div>
  <div class="field">Email</div>
  <span class="btn">Subscribe Now</span>
  <p class="note">Brindle Wares never shares with third parties any names and email addresses collected from this website, period! You have my name on that!</p>
</section>

<div class="products-tab box abs">
  <span>Our products</span>
  <i><svg width="32" height="18" viewBox="0 0 32 18"><path d="M3 3l13 11L29 3" fill="none" stroke="#fff" stroke-width="5"/></svg></i>
</div>

<h2 class="section-title abs">VIEW OUR MOST POPULAR <em>Kitchen Knives</em></h2>

<div class="card abs" style="left:88px;top:573px"><div class="photo" role="img" aria-label="Paring knife with dark handle on burl wood" style="background:radial-gradient(ellipse 60% 25% at 65% 65%,rgba(60,25,20,.45),transparent 70%),linear-gradient(135deg,#d9a661,#c08a4a 60%,#b57b3c)"></div><div class="price-bar"><b>Price : $244.00</b><span class="btn">Add to Cart</span></div></div>
<div class="card abs" style="left:290px;top:573px"><div class="photo" role="img" aria-label="Fixed blade knife with brown leather sheath on white" style="background:radial-gradient(ellipse 55% 35% at 35% 65%,rgba(130,70,40,.6),transparent 70%),linear-gradient(135deg,#f4f4f4,#dcd3cb 60%,#c7bfb8)"></div><div class="price-bar"><b>Price : $244.00</b><span class="btn">Add to Cart</span></div></div>
<div class="card abs" style="left:492px;top:573px"><div class="photo" role="img" aria-label="Set of kitchen knives laid on a wooden cutting board" style="background:repeating-linear-gradient(90deg,#c99c6a 0 22px,#d6b080 22px 44px)"></div><div class="price-bar"><b>Price : $244.00</b><span class="btn">Add to Cart</span></div></div>
<div class="card abs" style="left:693px;top:573px"><div class="photo" role="img" aria-label="Serrated utility knife with olive handle on dark ground" style="background:radial-gradient(ellipse 60% 30% at 55% 45%,rgba(110,105,70,.8),transparent 70%),linear-gradient(135deg,#2c2c2c,#3a3a34 55%,#333)"></div><div class="price-bar"><b>Price : $244.00</b><span class="btn">Add to Cart</span></div></div>

<div class="card abs" style="left:88px;top:760px"><div class="photo" role="img" aria-label="Curved knife resting on a dark leather sheath" style="background:radial-gradient(ellipse 55% 30% at 50% 55%,rgba(60,45,35,.75),transparent 70%),linear-gradient(135deg,#d5d5d5,#bdb8b4 60%,#a9a39e)"></div><div class="price-bar"><b>Price : $244.00</b><span class="btn">Add to Cart</span></div></div>
<div class="card abs" style="left:290px;top:760px"><div class="photo" role="img" aria-label="Knife with bone handle on a brown leather sheath" style="background:radial-gradient(ellipse 60% 30% at 50% 40%,rgba(130,60,35,.7),transparent 70%),linear-gradient(135deg,#f3f3f3,#e6e2de 60%,#eaeaea)"></div><div class="price-bar"><b>Price : $244.00</b><span class="btn">Add to Cart</span></div></div>
<div class="card abs" style="left:492px;top:760px"><div class="photo" role="img" aria-label="Knife with wooden handle on dark green surface" style="background:radial-gradient(ellipse 40% 20% at 75% 70%,rgba(190,145,95,.8),transparent 70%),linear-gradient(135deg,#2f4a4a,#344e4e 60%,#2c4545)"></div><div class="price-bar"><b>Price : $244.00</b><span class="btn">Add to Cart</span></div></div>
<div class="card abs" style="left:693px;top:760px"><div class="photo" role="img" aria-label="Knife sharpener and kitchen knives on a wooden board" style="background:radial-gradient(ellipse 45% 25% at 40% 20%,rgba(40,40,40,.7),transparent 70%),linear-gradient(135deg,#e2ddd6,#c29c6c 55%,#a98659)"></div><div class="price-bar"><b>Price : $244.00</b><span class="btn">Add to Cart</span></div></div>

<section class="feature-strip abs">
  <div class="feature" style="left:27px">
    <svg width="48" height="48" viewBox="0 0 48 48" role="img" aria-label="Disc"><circle cx="24" cy="24" r="22" fill="#e3e3e3" stroke="#bbb"/><circle cx="24" cy="24" r="5" fill="#fff" stroke="#bbb"/></svg>
    <span>Advanced Blade<br>Sharpening DVD</span>
  </div>
  <div class="feature" style="left:303px">
    <svg width="54" height="52" viewBox="0 0 54 52" role="img" aria-label="Knife"><path d="M4 6l28 28 3-3z" fill="#cfcfcf" stroke="#999"/><path d="M33 32l16 16" stroke="#222" stroke-width="5" stroke-linecap="round"/></svg>
    <span>Neck Knives &amp;<br>Kitchen Cutlery</span>
  </div>
  <div class="feature" style="left:578px;top:21px">
    <svg width="48" height="42" viewBox="0 0 48 42" role="img" aria-label="Settings"><rect width="48" height="42" rx="3" fill="#888"/><circle cx="24" cy="21" r="12" fill="none" stroke="#eee" stroke-width="5" stroke-dasharray="4 3"/><circle cx="24" cy="21" r="5" fill="#eee"/></svg>
    <span style="line-height:42px">Custom Knives</span>
  </div>
</section>

<footer class="site-footer abs">
  <h4 style="left:87px">QUICK LINKS</h4>
  <div class="f-links" style="left:88px">Home<br>Knives<br>Tools</div>
  <div class="f-links" style="left:202px">Instruction<br>About<br>Contact Dennis</div>
  <h4 style="left:436px">FOLLOW US ON</h4>
  <div class="socials"><span></span><span></span><span></span></div>
  <div class="social-text">Friendsy &nbsp;|&nbsp; Chirper &nbsp;|&nbsp; Workline</div>
  <div class="f-brand">BRINDLE<br>WARES</div>
  <div class="f-tag">17th Generation Tanabe Bladesmith</div>
  <div class="copy">Copyright © 2013 &nbsp;Brindle Wares. &nbsp;All rights reserved.</div>
</footer>

</body>
</html>
```